Präsentationsvorlagen für Strahlenschutzkurse
Zielgruppe
Wir bieten Strahlenschutzkurse in der Medizin an. Zielgruppe: Ärztinnen und Ärzte
Stichworte: Erwachsenenbildung, wissenschaftliche Inhalte
Aufgabenstellung
Wir benötigen eine Power-Point Präsentationsvorlage für unsere Kurse.
Auf allen Folien:
*Integration von unserem Logo
*Übernahme unseres bestehenden Farbkonzepts
*Feld für Überschrift
*kleines Textfeld für die Angabe der jeweiligen Quelle
Wir benötigen:
eine Folie nur mit Textfeld (z.B. Aufzählung, kurzer Text)
eine Folie Text mit Bild
eine Folie Bild bzw. Video
eine Folie mit einem wichtigen Lehrinhalt (wichtiger Text) - besondere Vorhebung erwünscht
eine Folie für Anfang bzw. Ende
HEX-CODE:
#4f93fe
#eea62f
#ffffff

```html
<!DOCTYPE html>
<html lang="de">
<head>
<meta charset="utf-8">
<title>Folie – Wichtiger Lehrinhalt</title>
<link href="https://fonts.googleapis.com/css2?family=Carlito:wght@400;700&display=swap" rel="stylesheet">
<style>
  :root {
    --blue: #4f93fe;
    --orange: #eea62f;
    --white: #ffffff;
    --navy: #36557e;
    --title: #3d5a80;
    --text: #1b1b1b;
    --footer: #9ba7b5;
    --bg-low: #e8ebef;
  }
  * { margin: 0; padding: 0; box-sizing: border-box; }
  html, body { width: 1200px; height: 675px; overflow: hidden; }
  body { font-family: "Carlito", "Calibri", sans-serif; }

  .slide {
    position: relative;
    width: 1200px;
    height: 675px;
    background: linear-gradient(to bottom, var(--white) 0%, var(--white) 58%, var(--bg-low) 100%);
    overflow: hidden;
  }

  .slide-title {
    position: absolute;
    left: 161px;
    top: 106px;
    font-size: 44px;
    font-weight: 400;
    color: var(--title);
    letter-spacing: 0.2px;
    white-space: nowrap;
  }

  .brand-mark {
    position: absolute;
    right: 36px;
    top: 84px;
    display: flex;
    align-items: center;
    gap: 8px;
    font-size: 17px;
    font-weight: 700;
    color: var(--title);
  }
  .brand-mark .dot {
    width: 14px; height: 14px; border-radius: 50%;
    background: var(--title);
  }

  .callout {
    position: absolute;
    left: 158px;
    top: 179px;
    width: 267px;
    height: 73px;
  }
  .callout svg { position: absolute; inset: 0; }
  .callout-label {
    position: relative;
    display: block;
    height: 65px;
    line-height: 65px;
    text-align: center;
    font-size: 35px;
    font-weight: 700;
    color: var(--white);
    padding-right: 28px;
  }

  .key-box {
    position: absolute;
    left: 162px;
    top: 279px;
    width: 893px;
    height: 211px;
    border-radius: 4px;
    padding: 8px;
    background: conic-gradient(var(--orange) 0deg 40deg, var(--blue) 77deg, var(--navy) 100deg 245deg, var(--blue) 258deg, var(--orange) 292deg 360deg);
  }
  .key-box-inner {
    width: 100%;
    height: 100%;
    background: var(--white);
    padding: 34px 33px;
  }
  .key-box-text {
    font-size: 24.5px;
    line-height: 30.5px;
    color: var(--text);
  }

  .footer {
    position: absolute;
    left: 0; right: 0; bottom: 0;
    height: 111px;
    background: var(--footer);
    color: var(--white);
  }
  .footer-brand {
    position: absolute;
    left: 30px;
    top: 41px;
    display: flex;
    align-items: center;
    gap: 8px;
    font-size: 16px;
    font-weight: 400;
    letter-spacing: 0.5px;
  }
  .footer-brand .dot {
    width: 14px; height: 14px; border-radius: 50%;
    background: var(--white);
  }
  .source-note {
    position: absolute;
    left: 881px;
    top: 48px;
    font-size: 19px;
  }
  .page-number {
    position: absolute;
    left: 1141px;
    top: 50px;
    font-size: 17px;
  }
</style>
</head>
<body>
<div class="slide">
  <h1 class="slide-title">Überschrift Folie mit wichtigen Lehrinhalt</h1>

  <div class="brand-mark"><span class="dot"></span>Brandholt &amp; Weyrich</div>

  <div class="callout">
    <svg width="267" height="73" viewBox="0 0 267 73" aria-hidden="true">
      <path d="M8 0 H259 Q267 0 267 8 V57 Q267 65 259 65 H110 L82 73 L48 65 H8 Q0 65 0 57 V8 Q0 0 8 0 Z" fill="#eea62f"/>
    </svg>
    <span class="callout-label">WICHTIG!</span>
  </div>

  <div class="key-box">
    <div class="key-box-inner">
      <p class="key-box-text">Lorem ipsum dolor sit amet, consetetur sadipscing elitr, sed diam nonumy eirmod tempor invidunt ut labore et dolore magna aliquyam erat, sed diam voluptua.</p>
    </div>
  </div>

  <footer class="footer">
    <div class="footer-brand"><span class="dot"></span>BRANDHOLT &amp; WEYRICH</div>
    <span class="source-note">Feld Quellangaben</span>
    <span class="page-number">6</span>
  </footer>
</div>
</body>
</html>
```